New Wix logo and website layout

I need a new logo design and a new, modern website layout design. I am a professional therapist providing remedial massage. I am Canadian but live in Australia & would like the logo to have a somewhat 'Canadian feel' to it (something subtle i.e. no flags) I currently have a maple tree leaf as my logo. my current website is cedarridgemassage.com.au. I need the website to work on mobile phones & traditional web browsers.

Target Market(s)

customers looking for remedial massage and manual lymphatic drainage

Industry/Entity Type

professional massage

Coding

Coded - Design and coding required

Font styles to use
Sans Serif

Colors
EB3D1F
EC4F4E
F09395
F8D3D4
FCEDEE

Requirements
Nice to have
• something subtle that indicates that I am canadian
Should not have
• no flags. nothing too bold

```html
<!DOCTYPE html>
<html lang="en">
<head>
<meta charset="utf-8">
<title>Cedar Ridge Massage – Remedial Massage</title>
<link href="https://fonts.googleapis.com/css2?family=PT+Serif:wght@400;700&family=Poppins:wght@400;500;600&display=swap" rel="stylesheet">
<style>
:root{
  --red:#EB3D1F;
  --red-soft:#EC4F4E;
  --rose:#F09395;
  --blush:#F8D3D4;
  --blush-light:#FCEDEE;
  --ink:#222;
  --muted:#555;
  --white:#fff;
  --black:#000;
}
*{margin:0;padding:0;box-sizing:border-box}
html,body{width:1200px;height:3569px;overflow:hidden}
body{position:relative;background:var(--white);font-family:"Poppins",sans-serif;color:var(--ink)}
.abs{position:absolute}
.serif{font-family:"PT Serif",serif}
.btn{position:absolute;display:flex;align-items:center;justify-content:center;background:var(--red);color:var(--white);border-radius:22px;font-family:"PT Serif",serif;font-weight:700;font-size:19px}

/* header */
.header{position:absolute;left:0;top:0;width:1200px;height:137px;background:var(--white)}
.brand{position:absolute;left:97px;top:34px;display:flex;align-items:center;gap:18px}
.brand-dot{width:64px;height:64px;border-radius:50%;background:var(--red)}
.brand-name{font-family:"PT Serif",serif;font-weight:700;font-size:23px;line-height:27px;text-align:center;color:var(--black)}
.topline{position:absolute;top:19px;display:flex;align-items:center;gap:14px;font-size:16px;color:#333;white-space:nowrap}
.topline .ic{width:30px;height:30px;border-radius:50%;background:var(--red);display:flex;align-items:center;justify-content:center}
.nav{position:absolute;top:78px;left:490px;display:flex;gap:50px;font-size:16px;color:#555}
.nav .active{color:var(--red);font-weight:600;position:relative}
.nav .active:after{content:"";position:absolute;left:0;right:0;top:-19px;height:2px;background:var(--red)}
.nav-rule{position:absolute;left:490px;top:61px;width:596px;height:1px;background:#e8e8e8}
.btn-contact{left:981px;top:73px;width:105px;height:30px;font-size:15px}

/* hero */
.hero-photo{position:absolute;left:0;top:137px;width:1200px;height:700px;background:linear-gradient(100deg,#ececec 0%,#f4f2f1 35%,#d8c2b4 62%,#c7a592 78%,#e9e6e4 100%)}
.hero-title{left:111px;top:308px;font-size:44px;font-weight:700;color:var(--red)}
.hero-text{left:111px;top:372px;width:402px;font-size:16.5px;line-height:26.5px;color:#222;text-align:justify}
.btn-hero{left:111px;top:497px;width:153px;height:42px}

/* services */
.section-title{position:absolute;left:0;width:1200px;text-align:center;font-family:"PT Serif",serif;font-weight:700;font-size:33px;color:var(--red);letter-spacing:.5px}
.service-card{position:absolute;top:1000px;width:305px;height:347px;background:var(--white);border-radius:22px;box-shadow:0 4px 18px rgba(0,0,0,.09);text-align:center}
.service-icon{position:absolute;left:98px;top:28px;width:108px;height:108px;border-radius:50%;background:var(--red);display:flex;align-items:center;justify-content:center}
.service-name{position:absolute;left:0;right:0;top:153px;font-family:"PT Serif",serif;font-weight:700;font-size:26px;color:#222}
.service-text{position:absolute;left:30px;right:30px;top:203px;font-size:15.5px;line-height:26px;color:#333}
.service-arrow{position:absolute;left:137px;top:296px}
.btn-more{left:524px;top:1386px;width:153px;height:42px}

/* about */
.about-title{left:665px;top:1648px;font-size:33px;font-weight:700;color:var(--red)}
.about-lead{left:665px;top:1702px;width:421px;font-size:15.5px;line-height:26.7px;font-weight:600;color:#111;text-align:justify}
.about-text{left:665px;top:1818px;width:421px;font-size:15.5px;line-height:26.7px;color:#333;text-align:justify}
.btn-read{left:665px;top:1967px;width:153px;height:42px}

/* fees */
.fee-card{position:absolute;top:2372px;width:229px;height:222px;background:var(--white);box-shadow:0 3px 16px rgba(0,0,0,.09);text-align:center}
.fee-name{position:absolute;left:0;right:0;top:50px;font-family:"PT Serif",serif;font-weight:700;font-size:19px;color:#111}
.fee-price{position:absolute;left:0;right:0;top:84px;font-family:"PT Serif",serif;font-weight:700;font-size:38px;color:var(--red)}
.fee-time{position:absolute;left:0;right:0;top:148px;display:flex;justify-content:center;align-items:center;gap:12px;font-family:"PT Serif",serif;font-weight:700;font-size:17px;color:#222}
.btn-book{top:2575px;width:134px;height:36px;font-size:16px}
.pager{position:absolute;top:2642px;width:24px;height:24px;border-radius:50%;display:flex;align-items:center;justify-content:center}

/* contact */
.contact-band{position:absolute;left:0;top:2753px;width:1200px;height:476px;background:#f8f0f1}
.contact-title{top:2814px;font-size:33px;font-weight:700;color:var(--red)}
.field{position:absolute;background:var(--white);border-bottom:4px solid #e2dede;font-size:15px;color:#555;padding:12px 20px}
.btn-submit{left:114px;top:3112px;width:152px;height:43px}
.touch-row{position:absolute;left:747px;display:flex;gap:22px;font-size:16.5px;line-height:28px;color:#222;white-space:nowrap}
.touch-ic{width:40px;height:40px;border-radius:50%;background:var(--red);flex:none;display:flex;align-items:center;justify-content:center}
.social{position:absolute;top:3055px;width:40px;height:40px;border-radius:50%;background:var(--red);color:var(--white);font-size:16px;font-weight:600;display:flex;align-items:center;justify-content:center}

/* footer */
.footer{position:absolute;left:0;top:3229px;width:1200px;height:340px;background:var(--black);color:var(--white)}
.footer-brand{position:absolute;left:0;width:1200px;top:84px;display:flex;justify-content:center;align-items:center;gap:16px;font-family:"PT Serif",serif;font-weight:700;font-size:23px}
.footer-brand .dot{width:54px;height:54px;border-radius:50%;background:var(--white)}
.footer-nav{position:absolute;left:0;width:1200px;top:184px;display:flex;justify-content:center;gap:36px;font-size:16.5px}
.footer-copy{position:absolute;left:0;width:1200px;top:260px;text-align:center;font-size:15px;font-weight:500}
.footer-badge{position:absolute;left:956px;top:256px;width:130px;height:30px;border:2px solid var(--white);border-radius:4px}
</style>
</head>
<body>

<header class="header">
  <div class="brand"><div class="brand-dot"></div><div class="brand-name">CEDAR RIDGE<br>MASSAGE</div></div>
  <div class="topline" style="left:450px">
    <span class="ic"><svg width="14" height="14" viewBox="0 0 24 24"><path fill="#fff" d="M6.6 10.8a15 15 0 0 0 6.6 6.6l2.2-2.2c.3-.3.7-.4 1-.2 1.1.4 2.3.6 3.6.6.6 0 1 .4 1 1V20c0 .6-.4 1-1 1A17 17 0 0 1 3 4c0-.6.4-1 1-1h3.5c.6 0 1 .4 1 1 0 1.2.2 2.4.6 3.6.1.3 0 .7-.2 1z"/></svg></span>
    <span style="margin-left:6px">0400 555 218</span>
  </div>
  <div class="topline" style="left:650px">
    <span class="ic"><svg width="14" height="12" viewBox="0 0 24 20"><rect x="2" y="2" width="20" height="16" rx="2" fill="none" stroke="#fff" stroke-width="2.4"/><path d="M3 4l9 7 9-7" fill="none" stroke="#fff" stroke-width="2.4"/></svg></span>
    <span style="margin-left:6px">hello@cedarridgemassage.com.au</span>
  </div>
  <div class="topline" style="left:999px;gap:8px">
    <span class="ic"><svg width="16" height="16" viewBox="0 0 24 24" fill="none" stroke="#fff" stroke-width="1.8"><circle cx="12" cy="12" r="9"/><path d="M3 12h18M12 3c3 3 3 15 0 18M12 3c-3 3-3 15 0 18"/></svg></span>
    <span style="font-size:13px;color:#777">⌄</span><span style="color:#777">Eng</span>
  </div>
  <div class="nav-rule"></div>
  <nav class="nav"><span class="active">Home</span><span>Remedial Massage</span><span>About Me</span><span>Fees</span></nav>
  <div class="btn btn-contact">Contact Us</div>
</header>

<div class="hero-photo" role="img" aria-label="Photo of a woman relaxing face down on a white towel while a therapist massages her back"></div>
<svg class="abs" style="left:0;top:700px" width="1200" height="180" viewBox="0 0 1200 180">
  <path d="M0 80 C 120 130, 250 150, 420 118 C 600 82, 700 40, 900 55 C 1050 65, 1150 40, 1200 0 L1200 180 L0 180 Z" fill="#fff"/>
  <path d="M0 75 C 100 120, 250 148, 420 128 C 560 112, 620 55, 800 50 C 950 46, 1100 50, 1200 26" fill="none" stroke="var(--red)" stroke-width="7"/>
</svg>
<h1 class="abs serif hero-title">Remedial Massage</h1>
<p class="abs hero-text">Remedial massage is used to help relieve tension and stress in the soft tissues of the body including muscles, tendons, ligaments and connective tissue.</p>
<div class="btn btn-hero">Get Started</div>

<h2 class="section-title" style="top:918px">OUR SERVICES</h2>
<div class="service-card" style="left:111px">
  <div class="service-icon"><svg width="60" height="50" viewBox="0 0 60 50" fill="#fff"><circle cx="34" cy="8" r="6"/><path d="M26 16h10l6 14h-8zM4 32h38v6H4zM44 28h12v16H44zM8 40h4v8H8zM36 40h4v8h-4zM6 26a5 5 0 1 1 0 .1z"/></svg></div>
  <div class="service-name">Remedial</div>
  <p class="service-text">Lorem ipsum dolor elit, sed do eiusmod tempor ut labore et dolore magna aliqua.</p>
  <svg class="service-arrow" width="34" height="20" viewBox="0 0 34 20"><circle cx="10" cy="10" r="9" fill="var(--rose)"/><path d="M6 10h24M22 3l8 7-8 7" fill="none" stroke="var(--red)" stroke-width="3"/></svg>
</div>
<div class="service-card" style="left:448px">
  <div class="service-icon"><svg width="62" height="46" viewBox="0 0 62 46" fill="#fff"><circle cx="28" cy="10" r="7"/><path d="M6 30c10-6 22-8 34-6l14-10 4 4-14 14c-14 0-26 2-38 6z"/></svg></div>
  <div class="service-name">Deep Tissue</div>
  <p class="service-text">Lorem ipsum dolor elit, sed do eiusmod tempor ut labore et dolore magna aliqua.</p>
  <svg class="service-arrow" width="34" height="20" viewBox="0 0 34 20"><circle cx="10" cy="10" r="9" fill="var(--rose)"/><path d="M6 10h24M22 3l8 7-8 7" fill="none" stroke="var(--red)" stroke-width="3"/></svg>
</div>
<div class="service-card" style="left:784px">
  <div class="service-icon"><svg width="40" height="62" viewBox="0 0 40 62" fill="#fff"><circle cx="16" cy="8" r="7"/><path d="M8 18h14v10c10 2 14 10 12 18-2 8-10 12-20 12H8z"/></svg></div>
  <div class="service-name">Pregnancy</div>
  <p class="service-text">Lorem ipsum dolor elit, sed do eiusmod tempor ut labore et dolore magna aliqua.</p>
  <svg class="service-arrow" width="34" height="20" viewBox="0 0 34 20"><circle cx="10" cy="10" r="9" fill="var(--rose)"/><path d="M6 10h24M22 3l8 7-8 7" fill="none" stroke="var(--red)" stroke-width="3"/></svg>
</div>
<div class="btn btn-more">View More</div>

<svg class="abs" style="left:0;top:1455px" width="1200" height="770" viewBox="0 0 1200 770">
  <defs><linearGradient id="aboutBg" x1="0" y1="0" x2="0" y2="1"><stop offset="0" stop-color="var(--blush)"/><stop offset="1" stop-color="var(--blush-light)"/></linearGradient></defs>
  <path d="M0 70 C 200 20, 450 40, 700 100 C 900 140, 1100 120, 1200 75 L1200 690 C 1000 740, 800 730, 600 700 C 350 660, 150 640, 0 620 Z" fill="url(#aboutBg)"/>
  <path d="M0 72 C 160 15, 380 20, 700 100" fill="none" stroke="var(--red)" stroke-width="22"/>
  <path d="M560 690 C 800 740, 1000 745, 1200 688" fill="none" stroke="var(--red)" stroke-width="9"/>
</svg>
<svg class="abs" style="left:134px;top:1628px" width="450" height="408" viewBox="0 0 450 408" role="img" aria-label="Portrait photo of the therapist in a dark uniform with arms folded">
  <defs><linearGradient id="portrait" x1="0" y1="0" x2="1" y2="1"><stop offset="0" stop-color="#8a6c58"/><stop offset=".5" stop-color="#3e3a3a"/><stop offset="1" stop-color="#1f1f22"/></linearGradient></defs>
  <path d="M60 50 C 20 80, 0 220, 20 300 C 40 360, 100 330, 110 300 L 90 60 Z" fill="var(--red)"/>
  <path d="M320 110 C 420 120, 470 230, 420 300 C 380 360, 320 340, 300 300 Z" fill="var(--red)"/>
  <path d="M200 8 C 300 5, 390 70, 410 160 C 430 250, 360 360, 260 400 C 170 430, 90 370, 60 300 C 30 230, 0 150, 60 80 C 100 30, 150 10, 200 8 Z" fill="url(#portrait)"/>
</svg>
<h2 class="abs serif about-title">ABOUT US</h2>
<p class="abs about-lead">I completed my training in Toronto, Canada in 1999 where I obtained a Diploma of Remedial Massage through the Northbridge College of Massage &amp; Hydrotherapy.</p>
<p class="abs about-text">Over the years, I have practiced in several different settings including medical centre, chiropractic clinic, spa and currently am a sole trader in my own practice. I have been helping my clients achieve better health through my treatments for several years.</p>
<div class="btn btn-read">Read More</div>

<h2 class="section-title" style="top:2296px">FEE SCHEDULE</h2>
<div class="fee-card" style="left:111px"><div class="fee-name">Remedial Massage</div><div class="fee-price">$70</div><div class="fee-time"><svg width="20" height="20" viewBox="0 0 20 20"><circle cx="10" cy="11" r="7" fill="none" stroke="#111" stroke-width="3"/><path d="M10 7v4h3" stroke="#111" stroke-width="2" fill="none"/><circle cx="3" cy="3" r="2.5" fill="#111"/><circle cx="17" cy="3" r="2.5" fill="#111"/></svg>30 min</div></div>
<div class="fee-card" style="left:360px"><div class="fee-name">Remedial Massage</div><div class="fee-price">$90</div><div class="fee-time"><svg width="20" height="20" viewBox="0 0 20 20"><circle cx="10" cy="11" r="7" fill="none" stroke="#111" stroke-width="3"/><path d="M10 7v4h3" stroke="#111" stroke-width="2" fill="none"/><circle cx="3" cy="3" r="2.5" fill="#111"/><circle cx="17" cy="3" r="2.5" fill="#111"/></svg>45 min</div></div>
<div class="fee-card" style="left:611px"><div class="fee-name">Remedial Massage</div><div class="fee-price">$110</div><div class="fee-time"><svg width="20" height="20" viewBox="0 0 20 20"><circle cx="10" cy="11" r="7" fill="none" stroke="#111" stroke-width="3"/><path d="M10 7v4h3" stroke="#111" stroke-width="2" fill="none"/><circle cx="3" cy="3" r="2.5" fill="#111"/><circle cx="17" cy="3" r="2.5" fill="#111"/></svg>60 min</div></div>
<div class="fee-card" style="left:860px"><div class="fee-name">Remedial Massage</div><div class="fee-price">$160</div><div class="fee-time"><svg width="20" height="20" viewBox="0 0 20 20"><circle cx="10" cy="11" r="7" fill="none" stroke="#111" stroke-width="3"/><path d="M10 7v4h3" stroke="#111" stroke-width="2" fill="none"/><circle cx="3" cy="3" r="2.5" fill="#111"/><circle cx="17" cy="3" r="2.5" fill="#111"/></svg>90 min</div></div>
<div class="btn btn-book" style="left:160px">Book Now</div>
<div class="btn btn-book" style="left:400px">Book Now</div>
<div class="btn btn-book" style="left:662px">Book Now</div>
<div class="btn btn-book" style="left:904px">Book Now</div>
<div class="pager" style="left:568px;background:var(--red)"><svg width="10" height="12" viewBox="0 0 10 12"><path d="M7 1L2 6l5 5" fill="none" stroke="#fff" stroke-width="2.4"/></svg></div>
<div class="pager" style="left:609px;background:var(--rose)"><svg width="10" height="12" viewBox="0 0 10 12"><path d="M3 1l5 5-5 5" fill="none" stroke="#fff" stroke-width="2.4"/></svg></div>

<div class="contact-band"></div>
<h2 class="abs serif contact-title" style="left:111px">CONTACT US</h2>
<div class="field" style="left:111px;top:2867px;width:289px;height:50px">First Name</div>
<div class="field" style="left:414px;top:2867px;width:290px;height:50px">Last Name</div>
<div class="field" style="left:111px;top:2927px;width:289px;height:50px">Phone Number</div>
<div class="field" style="left:414px;top:2927px;width:290px;height:50px">Email</div>
<div class="field" style="left:111px;top:2989px;width:593px;height:104px">Message</div>
<div class="btn btn-submit">Submit</div>

<h2 class="abs serif contact-title" style="left:747px">GET IN TOUCH</h2>
<div class="touch-row" style="top:2868px"><span class="touch-ic"><svg width="18" height="22" viewBox="0 0 18 22"><path d="M9 1a7 7 0 0 1 7 7c0 5-7 13-7 13S2 13 2 8a7 7 0 0 1 7-7z" fill="none" stroke="#fff" stroke-width="2"/><circle cx="9" cy="8" r="2.5" fill="#fff"/></svg></span><span>Dana Whitlock 24 Coral Street<br>Seaview VIC 3199</span></div>
<div class="touch-row" style="top:2930px"><span class="touch-ic"><svg width="18" height="18" viewBox="0 0 24 24"><path fill="none" stroke="#fff" stroke-width="2" d="M6.6 10.8a15 15 0 0 0 6.6 6.6l2.2-2.2c.3-.3.7-.4 1-.2 1.1.4 2.3.6 3.6.6v3.4A17 17 0 0 1 3 4h3.5c0 1.2.2 2.4.6 3.6z"/></svg></span><span style="line-height:26px">+1 888 888 8888</span></div>
<div class="touch-row" style="top:2990px"><span class="touch-ic"><svg width="20" height="16" viewBox="0 0 24 20"><rect x="2" y="2" width="20" height="16" rx="2" fill="none" stroke="#fff" stroke-width="2"/><path d="M3 4l9 7 9-7" fill="none" stroke="#fff" stroke-width="2"/></svg></span><span style="line-height:26px">hello@cedarridgemassage.com.au</span></div>
<div class="social" style="left:747px">F</div>
<div class="social" style="left:805px">T</div>
<div class="social" style="left:862px">L</div>
<div class="social" style="left:920px">I</div>

<footer class="footer">
  <div class="footer-brand"><span class="dot"></span><span>CEDAR RIDGE MASSAGE</span></div>
  <nav class="footer-nav"><span>Home</span><span>|</span><span>Remedial Massage</span><span>|</span><span>About Me</span><span>|</span><span>Fees</span><span>|</span><span>Contact</span></nav>
  <div class="footer-copy">©2022. ALL RIGHTS RESERVED.</div>
  <div class="footer-badge"></div>
</footer>

</body>
</html>
```